Upmarket Dessert Lounge needs a Business Card Design

We are an upmarket dessert lounge needing a business card to match our image.

We want something that is simple yet beautiful, feminine, classy, sophisticated and elegant. We want it to stand out and don't mind if it is bold.

The design should include our logo and colours of red or maroon with gold highlights. We don't mind if black is used.

Marlow & Quince

Target Market(s)

For those who like to indulge or treat themselves and give in to their temptations on good quality desserts.

Industry/Entity Type

Business

Requirements
Must have
• Must include our logo and our name

Marlow & Quince

M & Q

```html
<!DOCTYPE html>
<html lang="en">
<head>
<meta charset="utf-8">
<title>Marlow &amp; Quince — Business Card</title>
<link rel="stylesheet" href="https://fonts.googleapis.com/css2?family=Source+Sans+3:wght@400;600;700&display=swap">
<style>
  :root {
    --page-bg: #d9d9d9;
    --card-black: #000000;
    --maroon: #7b1416;
    --peach: #fed29b;
    --cream: #f7d8a2;
    --white: #ffffff;
    --font-text: "Source Sans 3", "Myriad Pro", Arial, sans-serif;
  }
  * { box-sizing: border-box; margin: 0; padding: 0; }
  html, body {
    width: 956px;
    height: 1200px;
    overflow: hidden;
    background: var(--page-bg);
    font-family: var(--font-text);
  }
  .canvas { position: relative; width: 956px; height: 1200px; }

  .card {
    position: absolute;
    left: 75px;
    width: 797px;
    height: 455px;
    border-radius: 28px;
    overflow: hidden;
    background: var(--card-black);
  }
  .card--front { top: 86px; }
  .card--back { top: 634px; }

  /* Front: black brand side */
  .brand-panel {
    position: absolute;
    left: 0; top: 0;
    width: 437px; height: 100%;
    background: var(--card-black);
  }
  .brand-name {
    position: absolute;
    color: var(--cream);
    font-weight: 600;
    white-space: nowrap;
    transform: translate(-50%, -50%);
  }
  .brand-panel .brand-name {
    left: 220px; top: 184px;
    font-size: 80px;
    letter-spacing: 1px;
  }
  .address {
    position: absolute;
    left: 0; width: 437px;
    top: 362px;
    text-align: center;
    color: var(--white);
    font-size: 19px;
    line-height: 28px;
  }

  .divider {
    position: absolute;
    left: 437px; top: 0;
    width: 5px; height: 100%;
    background: var(--maroon);
  }

  /* Front: contact side */
  .contact-panel {
    position: absolute;
    left: 442px; top: 0; right: 0; height: 100%;
    background: var(--peach);
    color: var(--maroon);
  }
  .person { position: absolute; left: 33px; top: 68px; }
  .person__name { font-size: 23px; font-weight: 700; line-height: 30px; }
  .person__role { font-size: 22px; font-weight: 400; line-height: 30px; letter-spacing: 0.5px; }

  .contact-list { position: absolute; left: 39px; list-style: none; font-size: 19px; line-height: 36px; }
  .contact-list--phones { top: 196px; }
  .contact-list--web { top: 346px; line-height: 33px; }
  .contact-list b { font-weight: 700; }

  /* Back */
  .card--back .brand-name {
    left: 398px; top: 228px;
    font-size: 46px;
    letter-spacing: 1px;
  }
</style>
</head>
<body>
<main class="canvas">
  <section class="card card--front" aria-label="Business card front">
    <div class="brand-panel">
      <p class="brand-name">M &amp; Q</p>
      <p class="address">0000, Street Name<br>City Name, Country Code.</p>
    </div>
    <div class="divider"></div>
    <div class="contact-panel">
      <div class="person">
        <p class="person__name">Your Name</p>
        <p class="person__role">Designation</p>
      </div>
      <ul class="contact-list contact-list--phones">
        <li><b>p</b> : 123-456-7890</li>
        <li><b>c</b> : 123-456-7890</li>
        <li><b>f</b> : 123-456-7890</li>
      </ul>
      <ul class="contact-list contact-list--web">
        <li><b>e</b> : name@yourwebsite.com</li>
        <li><b>w</b> : www.marlowandquince.com</li>
      </ul>
    </div>
  </section>

  <section class="card card--back" aria-label="Business card back">
    <p class="brand-name">MARLOW &amp; QUINCE</p>
  </section>
</main>
</body>
</html>
```